Flyer for Medical practice welcoming new patients

We need a DL size brochure designed for Medical practice to advertise that we are accepting new patients. Our practice has special interests in women's and children's health and seniors health. Our existing advertising materials are in the colour scheme of purples I have uploaded our logo which includes our colour scheme.

Target Market(s)

Versatile to target anyone looking for a small medical practice that offers continuous care of seeing the same Doctor every time

Industry/Entity Type

Advertising

Font styles to use
Serif

Colors
6b449b
876aae
b7a5cc

Requirements
Must have
• The practice logo of just the picture not Dr Petra Holcombe.
• Purple colour scheme.
• Practice name: Tarrabeen Medical Practice.
• Address: 147 Corlett Rd, Tarrabeen NSW 2500.
• Phone: 4871 6035.
• DL size brochure
• Welcoming new patients ( a strong emphasis needs to be placed on this)
• Nurse and onsite ECG's and lung function tests.
• Travel vaccines including yellow fever
• Bulk billing for tertiary students
• We would also like design to alter the text so that we can change the points to be reflect who we are targeting at the time.
Nice to have
• The practice logo with Dr Petra Holcombe somewhere not as a feature as the practice no longer goes under this name but is still well known as Dr Holcombe's.

```html
<!DOCTYPE html>
<html lang="en">
<head>
<meta charset="utf-8">
<title>Tarrabeen Medical Practice – New Patients</title>
<link rel="stylesheet" href="https://fonts.googleapis.com/css2?family=Carlito:wght@400;700&family=Roboto+Condensed:wght@700&family=Montserrat:wght@700&display=swap">
<style>
  :root {
    --purple-deep: #6b449b;
    --purple-mid: #876aae;
    --purple-soft: #b7a5cc;
    --lavender: #d8cde6;
    --lavender-pale: #e9e2f1;
    --ink-purple: #4f2f86;
    --white: #ffffff;
    --stage: #c4c4c4;
    --headline-shadow: #1f1236;
  }
  * { margin: 0; padding: 0; box-sizing: border-box; }
  html, body {
    width: 1200px; height: 1000px; overflow: hidden;
    background: var(--stage);
  }
  .banner {
    position: absolute; left: 347px; top: 30px;
    width: 440px; height: 925px;
    background: var(--white);
    overflow: hidden;
    font-family: "Carlito", "Calibri", sans-serif;
  }
  .banner__art { position: absolute; inset: 0; }
  .brand {
    position: absolute; left: 84px; top: 3px;
    display: flex; align-items: center; gap: 12px;
  }
  .brand__mark {
    width: 124px; height: 124px; border-radius: 50%;
    border: 3px solid var(--lavender);
  }
  .brand__name {
    color: var(--purple-mid);
    font-size: 27px; font-weight: 400; line-height: 1.15;
  }
  .headline {
    position: absolute; left: 0; right: 0; top: 244px;
    text-align: center; color: var(--white);
    font-family: "Roboto Condensed", "Arial Narrow", sans-serif;
    font-weight: 700; text-transform: uppercase;
    text-shadow: 2px 3px 0 var(--headline-shadow), 1px 1px 2px var(--headline-shadow);
    line-height: 1.15;
  }
  .headline__lead { font-size: 32px; display: block; }
  .headline__main { font-size: 37px; display: block; letter-spacing: -0.3px; }
  .services {
    position: absolute; left: 6px; top: 527px; width: 430px;
    list-style: none; color: var(--ink-purple);
  }
  .services__item {
    position: relative; padding-left: 19px;
    font-size: 21.5px; line-height: 28px;
  }
  .services__item + .services__item { margin-top: 35px; }
  .services__item::before {
    content: ""; position: absolute; left: 1px; top: 9px;
    width: 12px; height: 12px; border-radius: 50%;
    background: var(--purple-mid);
  }
  .contact {
    position: absolute; left: 7px; top: 862px;
    color: var(--white);
    font-family: "Montserrat", "Verdana", sans-serif;
    font-weight: 700; font-size: 14.5px; line-height: 26px;
  }
</style>
</head>
<body>
  <main class="banner">
    <svg class="banner__art" viewBox="0 0 440 925" width="440" height="925" aria-hidden="true">
      <defs>
        <linearGradient id="purpleBand" x1="0" y1="0" x2="0" y2="1">
          <stop offset="0" stop-color="#ab98cc"/>
          <stop offset="0.5" stop-color="#8d71b6"/>
          <stop offset="1" stop-color="#6d479d"/>
        </linearGradient>
        <linearGradient id="footerBand" x1="0" y1="0" x2="0" y2="1">
          <stop offset="0" stop-color="#a692c8"/>
          <stop offset="1" stop-color="#6a45a0"/>
        </linearGradient>
        <linearGradient id="footerFade" x1="0" y1="0" x2="0" y2="1">
          <stop offset="0" stop-color="#ffffff"/>
          <stop offset="1" stop-color="#e2e0e4"/>
        </linearGradient>
      </defs>
      <!-- main purple band -->
      <path d="M0,50 Q50,215 440,185 L440,438 Q360,368 220,370 Q50,376 0,470 Z" fill="url(#purpleBand)"/>
      <!-- top lavender swoosh -->
      <path d="M0,0 L8,0 Q50,188 440,174 L440,185 Q50,215 0,50 Z" fill="var(--lavender)"/>
      <!-- lower lavender swoosh -->
      <path d="M0,470 Q50,376 220,370 Q360,368 440,438 L440,446 Q360,382 220,382 Q60,390 0,505 Z" fill="var(--lavender)"/>
      <!-- footer -->
      <rect x="0" y="808" width="440" height="30" fill="url(#footerFade)"/>
      <rect x="0" y="838" width="440" height="87" fill="url(#footerBand)"/>
    </svg>

    <header class="brand">
      <span class="brand__mark"></span>
      <p class="brand__name">Tarrabeen<br>Medical Practice</p>
    </header>

    <h1 class="headline">
      <span class="headline__lead">We are now</span>
      <span class="headline__main">Accepting new patients!</span>
    </h1>

    <ul class="services">
      <li class="services__item">Nurse on site for ECG's, lung function tests, health assessments and much more</li>
      <li class="services__item">We offer travel vaccines including yellow fever</li>
      <li class="services__item">Bulk billing for tertiary students</li>
    </ul>

    <footer class="contact">
      <p>Address: 147 Corlett Rd, Tarrabeen NSW 2500</p>
      <p>Telephone: 4871 6035</p>
    </footer>
  </main>
</body>
</html>
```